Brightwater Care Partners, LLC Business Card update!

would like a classier business card. Our cards currently just have our logo and contact information. Need better use of color and creativity
Logo attached.

Target Market(s)

Potential clients, contacts, existing clients. We are a consulting company

Industry/Entity Type

Business

Contact Information for Business Card

We like our colors but just have a boring card with our logo and a white background. I want something that stands out.

Colors
ec1f27
757575

Requirements
Must have
• Color to stay consistent. Logo provided
Nice to have
• Just better use of color/ design

```html
<!DOCTYPE html>
<html lang="en">
<head>
<meta charset="utf-8">
<title>Brightwater Care Partners — Business Card</title>
<link rel="stylesheet" href="https://fonts.googleapis.com/css2?family=Saira+Semi+Condensed:wght@400;600&display=swap">
<style>
  :root {
    --brand-pink: #d4145f;
    --brand-gray: #757575;
    --card-white: #ffffff;
    --backdrop: #8f9091;
    --ink-white: #ffffff;
  }
  * { box-sizing: border-box; margin: 0; padding: 0; }
  html, body {
    width: 1200px;
    height: 771px;
    overflow: hidden;
  }
  body {
    background: var(--backdrop);
    font-family: "Saira Semi Condensed", sans-serif;
    display: flex;
    align-items: center;
    justify-content: center;
    gap: 40px;
  }
  .card {
    position: relative;
    width: 540px;
    height: 309px;
    background: var(--card-white);
    overflow: hidden;
    box-shadow: 0 6px 18px rgba(0, 0, 0, 0.25);
  }
  .card__art {
    position: absolute;
    inset: 0;
    width: 100%;
    height: 100%;
  }

  /* Front */
  .brand-lockup {
    position: absolute;
    display: flex;
    align-items: center;
    gap: 12px;
  }
  .brand-lockup__dot {
    flex: none;
    border-radius: 50%;
    background: var(--brand-gray);
  }
  .brand-lockup__name {
    color: var(--brand-pink);
    font-weight: 600;
    text-transform: uppercase;
    line-height: 1.02;
    letter-spacing: 0.5px;
  }
  .card--front .brand-lockup { top: 28px; left: 120px; }
  .card--front .brand-lockup__dot { width: 34px; height: 34px; }
  .card--front .brand-lockup__name { font-size: 25px; }

  .contact-list {
    position: absolute;
    left: 22px;
    top: 168px;
    list-style: none;
    color: var(--ink-white);
    font-size: 10.5px;
    letter-spacing: 0.6px;
    text-transform: uppercase;
  }
  .contact-list li {
    display: flex;
    align-items: center;
    gap: 7px;
    height: 16px;
  }
  .contact-list svg { width: 11px; height: 11px; flex: none; }
  .contact-list .is-lower { text-transform: none; }

  .card-holder {
    position: absolute;
    right: 26px;
    bottom: 22px;
    text-align: right;
    color: var(--ink-white);
    text-transform: uppercase;
  }
  .card-holder__name {
    font-size: 14px;
    font-weight: 600;
    letter-spacing: 1.5px;
  }
  .card-holder__title {
    font-size: 10px;
    letter-spacing: 2.5px;
  }

  /* Back */
  .card--back .brand-lockup {
    top: 50%;
    left: 50%;
    transform: translate(-50%, -50%);
    gap: 18px;
  }
  .card--back .brand-lockup__dot { width: 64px; height: 64px; }
  .card--back .brand-lockup__name { font-size: 38px; }
</style>
</head>
<body>

  <section class="card card--front" aria-label="Business card front">
    <svg class="card__art" viewBox="0 0 540 309" preserveAspectRatio="none" aria-hidden="true">
      <path class="swoosh" d="M0,118 C150,112 300,150 470,300 L540,309 L458,309 C300,170 160,128 0,126 Z" fill="var(--brand-gray)"/>
      <path class="band" d="M0,140 C170,136 330,190 540,226 L540,309 L0,309 Z" fill="var(--brand-pink)"/>
    </svg>

    <div class="brand-lockup">
      <span class="brand-lockup__dot"></span>
      <span class="brand-lockup__name">Brightwater<br>Care Partners</span>
    </div>

    <ul class="contact-list">
      <li>
        <svg viewBox="0 0 12 12"><path d="M6 0.8a3.6 3.6 0 0 0-3.6 3.6C2.4 7.2 6 11.2 6 11.2s3.6-4 3.6-6.8A3.6 3.6 0 0 0 6 0.8zm0 5a1.4 1.4 0 1 1 0-2.8 1.4 1.4 0 0 1 0 2.8z" fill="currentColor"/></svg>
        Suite 410, Harbor Bldg.
      </li>
      <li><svg viewBox="0 0 12 12"></svg>NY 10482</li>
      <li>
        <svg viewBox="0 0 12 12"><circle cx="6" cy="6" r="5.6" fill="currentColor"/><path d="M4 3.2l1 1.6-.6.7a4 4 0 0 0 2.1 2.1l.7-.6 1.6 1-.5 1C5.6 9 3 6.4 3 3.7z" fill="var(--brand-pink)"/></svg>
        212-555-0148
      </li>
      <li>
        <svg viewBox="0 0 12 12"><circle cx="6" cy="6" r="5.6" fill="currentColor"/><path d="M4 3.2l1 1.6-.6.7a4 4 0 0 0 2.1 2.1l.7-.6 1.6 1-.5 1C5.6 9 3 6.4 3 3.7z" fill="var(--brand-pink)"/></svg>
        212-555-0193
      </li>
      <li>
        <svg viewBox="0 0 12 12"><circle cx="6" cy="6" r="5.6" fill="currentColor"/><rect x="3.4" y="3" width="5.2" height="6" rx="0.6" fill="var(--brand-pink)"/></svg>
        212-555-0127
      </li>
      <li class="is-lower">
        <svg viewBox="0 0 12 12"><circle cx="6" cy="6" r="5.6" fill="currentColor"/><rect x="2.8" y="3.8" width="6.4" height="4.4" fill="var(--brand-pink)"/><path d="M2.8 3.8L6 6.4l3.2-2.6" stroke="currentColor" stroke-width="0.7" fill="none"/></svg>
        DREYES@BRIGHTWATERCARE.COM
      </li>
      <li>
        <svg viewBox="0 0 12 12"><circle cx="6" cy="6" r="5.6" fill="currentColor"/><circle cx="6" cy="6" r="3.2" fill="none" stroke="var(--brand-pink)" stroke-width="0.8"/><path d="M2.8 6h6.4M6 2.8v6.4" stroke="var(--brand-pink)" stroke-width="0.8"/></svg>
        www.brightwatercare.com
      </li>
    </ul>

    <div class="card-holder">
      <p class="card-holder__name">Daniel Reyes</p>
      <p class="card-holder__title">Owner / C.E.O</p>
    </div>
  </section>

  <section class="card card--back" aria-label="Business card back">
    <div class="brand-lockup">
      <span class="brand-lockup__dot"></span>
      <span class="brand-lockup__name">Brightwater<br>Care Partners</span>
    </div>
  </section>

</body>
</html>
```